Corvane Capital Business Cards

These are professional business cards that are for my family office.
Put fake emails and phone numbers as of now until I finalize those components. This family office controls my families investments, assets, and future. The cards should be professional.
..
.
.
.
I just uploaded another variation of a logo I would like to see as a business card to I am inbeteen which logo to use

Target Market(s)

business

Industry/Entity Type

business

Contact Information for Business Card

Professional, wealth related, finance related.

Requirements
Must have
• Logo

```html
<!DOCTYPE html>
<html lang="en">
<head>
<meta charset="utf-8">
<title>Corvane Capital Business Cards</title>
<link href="https://fonts.googleapis.com/css2?family=Cinzel:wght@400;600;700&display=swap" rel="stylesheet">
<style>
  :root {
    --backdrop: #3b3b3d;
    --navy: #1b1f2c;
    --paper: #ffffff;
    --dot-grey: #a6a6a6;
    --ink-soft: #2a2e3a;
  }
  * { margin: 0; padding: 0; box-sizing: border-box; }
  html, body { width: 1200px; height: 1059px; overflow: hidden; }
  body {
    background: var(--backdrop);
    font-family: 'Cinzel', 'Times New Roman', serif;
    position: relative;
  }
  .card {
    position: absolute;
    left: 256px;
    width: 690px;
    height: 394px;
    border-radius: 18px;
    overflow: hidden;
    box-shadow: 6px 10px 18px rgba(0,0,0,0.55);
  }
  .card--front { top: 100px; background: var(--paper); color: var(--navy); }
  .card--back { top: 537px; background: var(--navy); color: var(--paper); }

  .front-details {
    position: absolute;
    left: 20px;
    top: 0;
    width: 300px;
    text-align: center;
  }
  .company-name {
    margin-top: 32px;
    font-size: 30px;
    font-weight: 600;
    letter-spacing: 0.5px;
    line-height: 1;
  }
  .person-name {
    margin-top: 30px;
    font-size: 31px;
    font-weight: 600;
    line-height: 1;
  }
  .person-title {
    margin-top: 8px;
    font-size: 16px;
    letter-spacing: 0.6px;
    color: var(--ink-soft);
  }
  .icon-row {
    margin-top: 16px;
    display: flex;
    align-items: center;
    justify-content: center;
    gap: 4px;
  }
  .icon-row .rule { width: 62px; height: 2px; background: var(--navy); margin: 0 5px; }
  .icon-row .icon {
    width: 27px; height: 27px;
    border-radius: 6px;
    background: var(--navy);
    display: flex; align-items: center; justify-content: center;
  }
  .contact-list { margin-top: 12px; font-size: 16px; line-height: 28px; color: var(--ink-soft); }
  .contact-list .phone { font-size: 17px; }
  .divider { width: 205px; height: 2px; background: var(--navy); margin: 8px auto 12px; }
  .address { font-size: 16px; line-height: 28px; color: var(--ink-soft); letter-spacing: 0.4px; }

  .front-mark {
    position: absolute;
    left: 300px;
    top: 2px;
    width: 390px;
    height: 390px;
    border: 6px solid var(--navy);
    border-radius: 50%;
    display: flex;
    flex-direction: column;
    align-items: center;
    justify-content: center;
  }
  .front-mark .mark-name {
    font-size: 40px;
    font-weight: 600;
    line-height: 1.15;
    text-align: center;
    color: var(--navy);
    margin-right: 40px;
  }

  .back-ring {
    position: absolute;
    left: 245px;
    top: 63px;
    width: 212px;
    height: 212px;
    border: 4px solid var(--paper);
    border-radius: 50%;
  }
  .back-name {
    position: absolute;
    left: 0; right: 0;
    top: 300px;
    text-align: center;
    font-size: 40px;
    font-weight: 600;
    letter-spacing: 1px;
  }
</style>
</head>
<body>
  <section class="card card--front">
    <div class="front-details">
      <h1 class="company-name">Corvane Capital</h1>
      <h2 class="person-name">Elliot Harwood</h2>
      <p class="person-title">Managing Director</p>
      <div class="icon-row">
        <span class="rule"></span>
        <span class="icon" aria-label="Phone">
          <svg width="17" height="17" viewBox="0 0 24 24"><path fill="#fff" d="M6.6 10.8a15 15 0 0 0 6.6 6.6l2.2-2.2c.3-.3.7-.4 1-.2 1.1.4 2.3.6 3.6.6.6 0 1 .4 1 1V20c0 .6-.4 1-1 1A17 17 0 0 1 3 4c0-.6.4-1 1-1h3.5c.6 0 1 .4 1 1 0 1.3.2 2.5.6 3.6.1.3 0 .7-.2 1z"/></svg>
        </span>
        <span class="icon" aria-label="Email">
          <svg width="17" height="17" viewBox="0 0 24 24"><rect x="2" y="5" width="20" height="14" rx="2" fill="#fff"/><path d="M3 6l9 7 9-7" fill="none" stroke="#1b1f2c" stroke-width="1.8"/></svg>
        </span>
        <span class="icon" aria-label="Website">
          <svg width="17" height="17" viewBox="0 0 24 24" fill="none" stroke="#fff" stroke-width="1.8"><circle cx="12" cy="12" r="9"/><ellipse cx="12" cy="12" rx="4" ry="9"/><path d="M3 12h18"/></svg>
        </span>
        <span class="rule"></span>
      </div>
      <div class="contact-list">
        <p class="phone">123 456 789</p>
        <p>info@youremail.com</p>
        <p>www.yourwebsite.com</p>
      </div>
      <div class="divider"></div>
      <p class="address">Your address, City<br>State, Zip 1234</p>
    </div>
    <div class="front-mark">
      <p class="mark-name">Corvane<br>Capital</p>
    </div>
  </section>

  <section class="card card--back">
    <div class="back-ring"></div>
    <p class="back-name">Corvane Capital</p>
  </section>
</body>
</html>
```